Pet Care Business Post Card

We are a local San Antonio Texas based pet care company looking to introduce ourselves to potential clients. We are a husband and wife team with a lifetime of experience in our field and have been so professionally since 2006. Our primary services include dog walking and cat sitting services. We are also a provider of pet supplies and pet taxi services. More information about us is available on our website www.furlowpaws.com.
Updates

Project Deadline Extended
Reason: Looking for higher submission count

We want to utilize both sides with info and still have space for postage/address/barcode for mailing

Target Market(s)

The primary decision maker for our services is mostly female

Industry/Entity Type

Pet

Requirements
Must have
• We definitely want to utilize both sides of the post card and it will be for mailing

```html
<!DOCTYPE html>
<html lang="en">
<head>
<meta charset="utf-8">
<title>Furlow Paws Postcard</title>
<link rel="stylesheet" href="https://fonts.googleapis.com/css2?family=Archivo+Black&family=Jost:wght@400;500;600&display=swap">
<style>
:root{
  --backdrop:#23272f;
  --card:#ffffff;
  --olive:#85855f;
  --bronze:#9a6f36;
  --bronze-light:#c39557;
  --cream:#efe6da;
  --ink:#222222;
  --rule:#555555;
}
*{margin:0;padding:0;box-sizing:border-box}
html,body{width:1200px;height:1016px;overflow:hidden;background:var(--backdrop)}
.postcard{position:absolute;left:79px;top:90px;width:1042px;height:801px;background:var(--card);font-family:'Jost',sans-serif;color:var(--ink)}
.info-side{position:absolute;left:0;top:0;width:506px;height:698px;background:linear-gradient(to bottom,#ffffff 0px,#ffffff 210px,var(--cream) 600px)}
.hero-photo{position:absolute;left:0;top:0;width:503px;height:178px;background:linear-gradient(90deg,#f3ece6 0%,#c8a486 30%,#b87a4c 50%,#ebe4dc 75%,#ffffff 100%)}
.section-title{position:absolute;display:flex;align-items:center;gap:10px;font-family:'Archivo Black',sans-serif;font-size:22px;color:var(--olive);letter-spacing:.3px}
.section-title svg{width:32px;height:32px;flex:none}
.benefits{position:absolute;list-style:none;font-size:19px;line-height:21px}
.benefits li{position:relative;padding-left:19px;margin-bottom:9px}
.benefits li::before{content:"";position:absolute;left:0;top:7px;width:9px;height:9px;background:var(--bronze)}
.web-band{position:absolute;left:0;top:647px;width:506px;height:51px;background:linear-gradient(to bottom,var(--bronze-light),var(--bronze));color:#fff;font-weight:600;font-size:26px;text-align:center;line-height:51px;padding-right:40px;letter-spacing:.3px}
.sender{position:absolute;left:536px;top:38px}
.sender h1{font-weight:600;font-size:32px;color:var(--olive);letter-spacing:.3px;line-height:40px}
.sender .city{font-size:17px;margin-top:6px}
.contact{list-style:none;font-size:18px;line-height:24px}
.contact li{position:relative;padding-left:22px}
.contact li::before{content:"";position:absolute;left:1px;top:8px;width:10px;height:10px;background:var(--olive)}
.contact b{font-weight:600}
.stamp-box{position:absolute;left:900px;top:51px;width:108px;height:136px;border:1px solid #444}
.address-line{position:absolute;left:637px;width:304px;border-top:1px solid var(--rule)}
</style>
</head>
<body>
<main class="postcard">
  <section class="info-side">
    <div class="hero-photo" role="img" aria-label="Photo of a cat and a dog eating from metal bowls"></div>

    <h2 class="section-title" style="left:26px;top:200px">
      <svg viewBox="0 0 32 32" aria-hidden="true"><circle cx="16" cy="16" r="14.5" fill="#fff" stroke="#9a6f36" stroke-width="2"/><ellipse cx="16" cy="19.5" rx="5" ry="4" fill="#9a6f36"/><circle cx="10.5" cy="13.5" r="2" fill="#9a6f36"/><circle cx="14" cy="10.5" r="2" fill="#9a6f36"/><circle cx="18" cy="10.5" r="2" fill="#9a6f36"/><circle cx="21.5" cy="13.5" r="2" fill="#9a6f36"/></svg>
      ADVANTAGES OF A PET SITTER
    </h2>
    <ul class="benefits" style="left:48px;top:238px">
      <li>Reduced stress on your pet</li>
      <li>Pet feel most comfortable and secure</li>
      <li>With familiar sights, sounds and smells</li>
      <li>No "travel" trauma</li>
      <li>Minimal exposure to illnesses</li>
    </ul>

    <h2 class="section-title" style="left:24px;top:405px">
      <svg viewBox="0 0 32 32" aria-hidden="true"><circle cx="16" cy="16" r="14.5" fill="#fff" stroke="#9a6f36" stroke-width="2"/><ellipse cx="16" cy="19.5" rx="5" ry="4" fill="#9a6f36"/><circle cx="10.5" cy="13.5" r="2" fill="#9a6f36"/><circle cx="14" cy="10.5" r="2" fill="#9a6f36"/><circle cx="18" cy="10.5" r="2" fill="#9a6f36"/><circle cx="21.5" cy="13.5" r="2" fill="#9a6f36"/></svg>
      &nbsp;ADVANTAGES FOR YOU
    </h2>
    <ul class="benefits" style="left:53px;top:443px;width:430px">
      <li>Free initial consultation in your home.</li>
      <li>We discuss your pet care need</li>
      <li>Altering of household lighting and blinds for a lived in look</li>
      <li>All services include watering indoor plants, retrieving mail, taking out the garbage and more...</li>
    </ul>

    <div class="web-band">WWW.FURLOWPAWS.COM</div>
  </section>

  <section class="sender">
    <h1>Furlow Paws LLC</h1>
    <p class="city">San Antonio, TX</p>
    <ul class="contact">
      <li><b>Telephone:</b> (210) 555-0142</li>
      <li><b>E-Fax:</b> (210) 555-0178</li>
      <li><b>E-Mail:</b> care@furlowpaws.com</li>
    </ul>
  </section>

  <div class="stamp-box"></div>
  <div class="address-line" style="top:342px"></div>
  <div class="address-line" style="top:408px"></div>
  <div class="address-line" style="top:476px"></div>
</main>
</body>
</html>
```